Garlic Farm for Farm Sales/Restaurant sales

Need a professional, but appealing to agriculture world. We are selling 27 kinds of Organic Garlic from a farm in Simla,CO. I have uploaded logo and business information-we are going to need a template, because I will need to use it for four separate people.
-We are trying to appeal to Farm to table restaurants
-As well as growers/farmers

Target Market(s)

Agriculture Sales/Restaurants-Organic

Industry/Entity Type

Agriculture

Contact Information for Business Card

Want it to look more unique then your average kelto stock card- I want it to look amazing

Font styles to use
Sans Serif

Colors
0455a3
ec1f27
fbed22
ffffff

Requirements
Must have
• Just be creative
Nice to have
• Colorful
Should not have
• plain

```html
<!DOCTYPE html>
<html lang="en">
<head>
<meta charset="utf-8">
<title>Prairie Crest Garlic – Business Card</title>
<link rel="stylesheet" href="https://fonts.googleapis.com/css2?family=Open+Sans:wght@400;600;700&display=swap">
<style>
  :root {
    --backdrop: #ecebe8;
    --card-red: #c10c2f;
    --card-red-deep: #a90a28;
    --card-navy: #0c2f63;
    --accent-yellow: #fdd800;
    --accent-coral: #d9524c;
    --paper: #ffffff;
    --ink-white: #ffffff;
  }
  * { box-sizing: border-box; margin: 0; padding: 0; }
  html, body { width: 1200px; height: 987px; overflow: hidden; }
  body {
    background: var(--backdrop);
    font-family: "Open Sans", Arial, sans-serif;
    position: relative;
  }
  .card {
    position: absolute;
    width: 615px;
    height: 351px;
    overflow: hidden;
    box-shadow: 0 2px 6px rgba(0,0,0,.18);
  }
  .card-front { left: 293px; top: 130px; background: var(--card-red); }
  .card-back  { left: 292px; top: 505px; background: var(--paper); }

  .front-band {
    position: absolute; left: 0; top: 0; width: 150px; height: 100%;
    background: var(--card-navy);
  }
  .front-mark {
    position: absolute; left: 14px; top: 4px; width: 343px; height: 343px;
    border-radius: 50%;
    background: var(--card-red-deep);
    border: 12px solid var(--accent-coral);
    box-shadow: inset 0 0 0 6px var(--card-navy);
    display: flex; align-items: center; justify-content: center;
  }
  .front-mark-name {
    color: var(--accent-yellow);
    font-weight: 700; font-size: 38px; line-height: 44px;
    text-align: center; letter-spacing: .5px;
  }

  .contact {
    position: absolute; right: 37px; top: 64px;
    text-align: right; color: var(--ink-white);
  }
  .contact-name {
    color: var(--accent-yellow); font-weight: 600; font-size: 22px;
    letter-spacing: .3px; line-height: 28px;
  }
  .contact-title { font-size: 16px; line-height: 22px; margin-bottom: 12px; }
  .contact-address { font-size: 15.5px; line-height: 23px; margin-bottom: 9px; }
  .contact-line {
    display: flex; justify-content: flex-end; align-items: center; gap: 8px;
    font-size: 15.5px; line-height: 23px;
  }
  .contact-line svg { width: 15px; height: 15px; flex: none; }
  .social-row {
    display: flex; justify-content: flex-end; gap: 4px; margin-top: 19px;
  }
  .social-dot {
    width: 21px; height: 21px; border-radius: 50%;
    background: var(--accent-yellow);
    box-shadow: inset 0 0 0 5px var(--accent-yellow), inset 0 0 0 7px var(--card-red);
  }

  .brand {
    position: absolute; left: 0; right: 0; top: 76px;
    display: flex; flex-direction: column; align-items: center;
  }
  .brand-circle {
    width: 94px; height: 94px; border-radius: 50%;
    background: var(--card-red);
    border: 6px solid var(--accent-coral);
  }
  .brand-name {
    margin-top: 20px;
    font-size: 32px; font-weight: 600; color: var(--card-navy);
    letter-spacing: .2px;
  }
</style>
</head>
<body>

<section class="card card-front">
  <div class="front-band"></div>
  <div class="front-mark">
    <p class="front-mark-name">Prairie Crest<br>Garlic</p>
  </div>

  <div class="contact">
    <p class="contact-name">DANA ORTLEY</p>
    <p class="contact-title">CEO/FOUNDER</p>
    <p class="contact-address">P.O. Box 112<br>Larkfield, CO&nbsp; 80412</p>
    <p class="contact-line">555-014-2739
      <svg viewBox="0 0 24 24"><path fill="var(--accent-yellow)" d="M6.6 10.8a15.1 15.1 0 0 0 6.6 6.6l2.2-2.2c.3-.3.7-.4 1-.2 1.1.4 2.3.6 3.6.6.6 0 1 .4 1 1V20c0 .6-.4 1-1 1A17 17 0 0 1 3 4c0-.6.4-1 1-1h3.5c.6 0 1 .4 1 1 0 1.3.2 2.5.6 3.6.1.3 0 .7-.2 1z"/></svg>
    </p>
    <p class="contact-line">Dana@PCGarlic.com
      <svg viewBox="0 0 24 24"><rect x="2" y="5" width="20" height="14" rx="1" fill="var(--accent-yellow)"/><path d="M3 6l9 7 9-7" fill="none" stroke="var(--card-red)" stroke-width="1.8"/></svg>
    </p>
    <p class="contact-line">www.PCGarlic.com
      <svg viewBox="0 0 24 24"><circle cx="12" cy="12" r="10" fill="var(--accent-yellow)"/><path d="M2 12h20M12 2c3 3 3 17 0 20M12 2c-3 3-3 17 0 20" fill="none" stroke="var(--card-red)" stroke-width="1.5"/></svg>
    </p>
    <div class="social-row">
      <span class="social-dot"></span><span class="social-dot"></span><span class="social-dot"></span><span class="social-dot"></span>
    </div>
  </div>
</section>

<section class="card card-back">
  <div class="brand">
    <div class="brand-circle"></div>
    <p class="brand-name">prairie crest garlic</p>
  </div>
</section>

</body>
</html>
```